Stationery Design Project for High End Wealth Management Firm

We need a stationery design for our high-end wealth management firm. Our clientele are affluent and our brand is built around providing investment services with world-class service.

The final concepts should provide a business card, letterhead, and envelope.

We like the idea of having text on the front and back and we MUST have black front and back business cards.
For the business card we have the following that needs to be included:
Company Logo & Tagline
Employee Name
Employee title
Employee Email
Website
2 seperate office cities, addresses, and phone numbers
Financial disclosure (small print)

Having black envelopes would be neat, but black is not a must for the envelopes.
Updates

Project Deadline Extended
Reason: To give the concept one more day of revisions.

Project Deadline Extended
Reason: To allow for more concepts and designs.

Target Market(s)

High Net Worth

Industry/Entity Type

Business

Requirements
Must have
• The following disclosure must be on the back of the card in small print:

Investment Advisory Services offered through Harrowfield Asset Partners LLC, a NFR Registered Investment Advisor. Vantory Wealth Management LLC is not affiliated with Harrowfield Asset Partners LLC.

Black business cards are also a must have.

Please utilize each of the 3 components of our logo in the design.

Please use our white background logo elements when designing our letterhead if you need them.
Nice to have
• Please use our company colors when designing. Utilize a combination of the elements of our logo that we have attached.

We are going to be printing our business cards on letterpress.

```html
<!DOCTYPE html>
<html lang="en">
<head>
<meta charset="utf-8">
<title>Vantory Wealth Management – Business Card Options</title>
<link rel="stylesheet" href="https://fonts.googleapis.com/css2?family=Marcellus&family=Arimo:wght@400;700&display=swap">
<style>
  :root {
    --board: #6abd45;
    --card: #060607;
    --gold: #f2c650;
    --gold-deep: #b8741f;
    --gold-light: #f6d77a;
    --silver: #d6d6d6;
    --ink: #16120a;
    --muted: #a9a9a9;
    --label: #0b0b0b;
  }
  * { box-sizing: border-box; margin: 0; padding: 0; }
  html, body { width: 1200px; height: 747px; overflow: hidden; }
  body {
    position: relative;
    background: var(--board);
    font-family: "Arimo", Arial, sans-serif;
  }
  .option-label {
    position: absolute;
    font-weight: 700;
    font-size: 22px;
    color: var(--label);
  }
  .card {
    position: absolute;
    width: 518px;
    height: 295px;
    background: var(--card);
    border-radius: 22px;
    overflow: hidden;
    box-shadow: 3px 4px 6px rgba(0,0,0,.35);
  }
  .brand {
    position: absolute;
    left: 0; right: 0;
    display: flex;
    justify-content: center;
    align-items: center;
    gap: 10px;
    font-family: "Arimo", Arial, sans-serif;
    font-weight: 400;
    font-size: 22px;
    letter-spacing: 1.5px;
    color: var(--silver);
    white-space: nowrap;
  }
  .brand-mark {
    width: 10px; height: 10px;
    background: var(--gold);
    border-radius: 50%;
  }
  .brand.small {
    left: 26px; right: auto;
    justify-content: flex-start;
    font-size: 15px;
    letter-spacing: 1px;
    gap: 8px;
  }
  .brand.small .brand-mark { width: 8px; height: 8px; }
  .tagline {
    position: absolute;
    left: 0; right: 0;
    text-align: center;
    font-size: 15px;
    color: var(--gold);
  }
  .gold-band {
    position: absolute;
    left: 0; right: 0;
    background: linear-gradient(90deg, var(--gold-deep) 0%, var(--gold-light) 35%, var(--gold) 60%, var(--gold-deep) 100%);
    border-top: 2px solid #2a1a05;
    border-bottom: 2px solid #2a1a05;
    box-shadow: 0 -3px 0 #8a5a14, 0 3px 0 #8a5a14;
  }
  .gold-band .tagline { color: var(--ink); }

  /* back of card */
  .person { position: absolute; left: 26px; top: 72px; font-family: "Marcellus", Georgia, serif; }
  .person-name { font-size: 19px; color: var(--silver); letter-spacing: .5px; }
  .person-title { font-family: "Arimo", Arial, sans-serif; font-size: 12px; color: var(--muted); margin-top: 2px; }
  .disclosure {
    position: absolute; right: 17px; top: 33px; width: 209px;
    font-size: 10px; line-height: 12.3px; color: #cfcfcf; text-align: justify;
  }
  .band-contact { position: absolute; color: var(--ink); font-size: 12.5px; line-height: 17px; }
  .band-contact.left { left: 20px; top: 11px; }
  .band-contact.right { right: 18px; top: 19px; text-align: right; font-size: 13px; line-height: 19px; }
  .row { display: flex; align-items: center; gap: 4px; }
  .right .row { justify-content: flex-end; }
  .icon { width: 11px; height: 11px; flex: none; }
  .office {
    position: absolute; right: 26px; top: 206px; text-align: right;
    color: var(--gold); font-size: 12.5px; line-height: 17px;
  }
  .office .row { justify-content: flex-end; gap: 6px; }
  .office .phones { margin-top: 7px; }
</style>
</head>
<body>

<div class="option-label" style="left:75px; top:15px;">Option 1</div>
<div class="option-label" style="left:67px; top:696px;">Option 2</div>
<div class="option-label" style="left:632px; top:696px;">Option 3</div>

<!-- Option 1 front -->
<section class="card" style="left:57px; top:56px;">
  <div class="brand" style="top:122px;">
    <span class="brand-mark"></span>
    <span class="brand-name">VANTORY WEALTH MANAGEMENT</span>
  </div>
  <p class="tagline" style="top:218px;">Trusted Wealth Stewardship for Discerning Families</p>
</section>

<!-- Card back -->
<section class="card" style="left:607px; top:62px;">
  <div class="person">
    <p class="person-name">PERSONS NAME</p>
    <p class="person-title">Designation</p>
  </div>
  <p class="disclosure">Investment Advisory Services offered through Harrowfield Asset Partners LLC, a NFR Registered Investment Advisor. Vantory Wealth Management LLC is not affiliated with Harrowfield Asset Partners LLC</p>

  <div class="gold-band" style="top:121px; height:71px;">
    <div class="band-contact left">
      <p>City name, State name, Country name&nbsp; 34236</p>
      <p class="row">
        <svg class="icon" viewBox="0 0 12 12"><path d="M2.5 1h2l1 3-1.3 1a6 6 0 0 0 2.8 2.8l1-1.3 3 1v2a1 1 0 0 1-1 1A9.5 9.5 0 0 1 1.5 2a1 1 0 0 1 1-1z" fill="currentColor"/></svg>
        234.567.8901&nbsp;
        <svg class="icon" viewBox="0 0 12 12"><rect x="1" y="4" width="10" height="6" rx="1" fill="currentColor"/><rect x="3" y="1" width="6" height="3" fill="currentColor"/></svg>
        234.567.8901
      </p>
      <p class="row">
        <svg class="icon" viewBox="0 0 12 12"><rect x="3" y="0.5" width="6" height="11" rx="1" fill="currentColor"/></svg>
        234.567.8901
      </p>
    </div>
    <div class="band-contact right">
      <p class="row">
        <svg class="icon" viewBox="0 0 12 12"><rect x="1" y="2.5" width="10" height="7" fill="none" stroke="currentColor" stroke-width="1.2"/><path d="M1 3l5 4 5-4" fill="none" stroke="currentColor" stroke-width="1.2"/></svg>
        name@VantoryWealth.com
      </p>
      <p>www.VANTORYWEALTH.COM</p>
    </div>
  </div>

  <div class="brand small" style="top:228px;">
    <span class="brand-mark"></span>
    <span class="brand-name">VANTORY WEALTH MANAGEMENT</span>
  </div>
  <div class="office">
    <p>1626 City name, State name</p>
    <p>Country name&nbsp; 34236</p>
    <div class="phones">
      <p class="row">234.567.8901
        <svg class="icon" viewBox="0 0 12 12"><path d="M2.5 1h2l1 3-1.3 1a6 6 0 0 0 2.8 2.8l1-1.3 3 1v2a1 1 0 0 1-1 1A9.5 9.5 0 0 1 1.5 2a1 1 0 0 1 1-1z" fill="currentColor"/></svg>
      </p>
      <p class="row">234.567.8901
        <svg class="icon" viewBox="0 0 12 12"><rect x="1" y="4" width="10" height="6" rx="1" fill="currentColor"/><rect x="3" y="1" width="6" height="3" fill="currentColor"/></svg>
      </p>
    </div>
  </div>
</section>

<!-- Option 2 front -->
<section class="card" style="left:53px; top:389px;">
  <div class="brand" style="top:120px;">
    <span class="brand-mark"></span>
    <span class="brand-name">VANTORY WEALTH MANAGEMENT</span>
  </div>
  <div class="gold-band" style="top:232px; height:34px;">
    <p class="tagline" style="top:7px;">Trusted Wealth Stewardship for Discerning Families</p>
  </div>
</section>

<!-- Option 3 front -->
<section class="card" style="left:606px; top:389px;">
  <div class="brand" style="top:120px;">
    <span class="brand-mark"></span>
    <span class="brand-name">VANTORY WEALTH MANAGEMENT</span>
  </div>
  <p class="tagline" style="top:218px;">Trusted Wealth Stewardship for Discerning Families</p>
</section>

</body>
</html>
```